Torvane Email Signature Banners – Fabrication Capability Series

www.Torvane.com.au is an Australian engineering and fabrication company specialising in fabrication and welding of :
steel piping spools,
skids and frames,
small volume process steel tanks
and general steel fabrication
We require four distinct banner designs for use in Microsoft Lintaro email signatures. Each banner will highlight a specific capability while maintaining a consistent brand identity.
Deliverables
Four banners total:
Piping Spools Fabrication – focus on precision welding and stainless steel pipework
Skid & Frames Fabrication – highlight skid systems and structural frames
Small Steel Tanks Fabrication – show fabricated tanks and workshop craftsmanship
General Fabrication Solutions – broad steel fabrication theme for company-wide use
Dimensions: 600–700 px wide × 100 px high
Format: PNG (preferred), small file size prefered
Resolution: 72 dpi
Background: non-transparent, industrial or workshop setting
Text examples:
1. Piping Spools Fabrication
Option A: “Expert Fabrication Solutions for Process Piping”
Option B: “Precision Welding for Complex Systems”
Option C: “Delivering Quality in Every Spool”
Option D: “Engineered for Flow, Built for Strength”
2. Skid & Frames Fabrication
Option A: “Custom Engineered Modular Systems”
Option B: “Built Strong. Designed Smart.”
Option C: “Reliable Frames for Industrial Performance”
Option D: “Modular Fabrication for Seamless Integration”
3. Small Steel Tanks Fabrication
Option A: “Precision Built for Your Needs”
Option B: “Compact Strength. Proven Durability.”
Option C: “Fabricated for Performance and Longevity”
Option D: “Small Tanks. Big Reliability.”
4. General Fabrication Solutions
Option A: “Quality Craftsmanship, Proven Results”
Option B: “Your Partner in Precision Fabrication”
Option C: “Engineering Excellence in Every Weld”
Option D: “Australian Fabrication. Global Standards.”
Style Direction
Clean, professional, and engineering‑focused
Use Torvane brand colours
Blend photo realism with vector clarity (no heavy gradients)
Include subtle industrial textures or workshop imagery
Typography: bold sans‑serif, legible at small scale
Usage Context
These banners will appear at the bottom of staff email signatures via Lintaro Email Signature Tool for Microsoft 365, so clarity and fast loading are essential. No Logo is required in the banners.
Reference
Existing Torvane signature is attached. Colour palette to match the signature style and logo.
Target Market(s)
Engineering and construction companies,
Industry/Entity Type
Engineering fabrication design
Look and feel

```html
<!DOCTYPE html>
<html lang="en">
<head>
<meta charset="utf-8">
<title>Piping Spools Fabrication Banner</title>
<link rel="stylesheet" href="https://fonts.googleapis.com/css2?family=Montserrat:wght@400;600;700&display=swap">
<style>
  :root {
    --brand-blue: #1a5fb4;
    --brand-blue-light: #2f80d4;
    --text-grey: #4a4a4a;
    --paper: #ffffff;
    --steel-dark: #3c4650;
    --steel-mid: #7e8a96;
    --steel-light: #c7ced6;
  }
  html, body {
    margin: 0;
    padding: 0;
    width: 1200px;
    height: 171px;
    overflow: hidden;
    background: var(--paper);
  }
  .banner {
    position: relative;
    width: 1200px;
    height: 171px;
    overflow: hidden;
    background: var(--paper);
    font-family: "Montserrat", Arial, sans-serif;
  }
  .banner__photo {
    position: absolute;
    left: 0;
    top: 0;
    width: 620px;
    height: 171px;
    background:
      linear-gradient(90deg, rgba(255,255,255,0) 0%, rgba(255,255,255,0) 55%, rgba(255,255,255,0.85) 85%, var(--paper) 100%),
      linear-gradient(180deg, var(--steel-light) 0%, var(--steel-mid) 45%, var(--steel-dark) 100%);
  }
  .banner__shapes {
    position: absolute;
    left: 0;
    top: 0;
    width: 1200px;
    height: 171px;
  }
  .banner__copy {
    position: absolute;
    left: 619px;
    top: 26px;
  }
  .headline {
    margin: 0;
    font-weight: 700;
    font-size: 33px;
    line-height: 39px;
    letter-spacing: 1.5px;
    color: var(--brand-blue);
  }
  .headline__sub {
    display: block;
    font-weight: 400;
    color: var(--brand-blue-light);
  }
  .capability {
    margin: 10px 0 0;
    font-weight: 400;
    font-size: 27px;
    letter-spacing: 0.5px;
    color: var(--text-grey);
  }
  .series-code {
    position: absolute;
    right: 6px;
    bottom: 6px;
    font-size: 9px;
    font-weight: 600;
    color: var(--paper);
  }
</style>
</head>
<body>
  <div class="banner">
    <div class="banner__photo" role="img" aria-label="Welder in a helmet welding a large stainless steel pipe spool in a workshop"></div>

    <svg class="banner__shapes" viewBox="0 0 1200 171" aria-hidden="true">
      <polygon points="634,0 751,0 688,40" fill="var(--brand-blue)"/>
      <polygon points="1123,171 1200,171 1200,96" fill="var(--brand-blue)"/>
    </svg>

    <div class="banner__copy">
      <h1 class="headline">PRECISION WELDING<span class="headline__sub">FOR COMPLEX SYSTEMS</span></h1>
      <p class="capability">Piping Spools Fabrication</p>
    </div>

    <span class="series-code">C62</span>
  </div>
</body>
</html>
```